Retail Jewelry Business Card Design Project

We are in need of a new business card design for a retail jewelry store. This store is in the business of fine jewelry including but not specific to bridal jewelry, diamonds, designer jewelry and watches.

This store has been in business for 20 years but continues to strive for a modern professional appeal. The main colors use for this business are a royal blue, white and silver.

Target Market(s)

Target market is ages 18-50

Industry/Entity Type

Jewelry

Requirements
Must have
• Sales Person Name
Sales Person Email Address

Store Address
Store Phone
Website

Standard business card size. No odd shapes or sizes.
Nice to have
• Overall modern feel for card.

We have thought that a design with a nice feature of the logo on the back of the card would be nice but open to ideas.
Should not have
• No specific images of jewelry should be used.

```html
<!DOCTYPE html>
<html lang="en">
<head>
<meta charset="utf-8">
<title>Marlow Avery Fine Jewelry – Business Cards</title>
<link href="https://fonts.googleapis.com/css2?family=Lora:wght@400;500&family=Open+Sans:wght@400&display=swap" rel="stylesheet">
<style>
  :root {
    --royal: #2a23a8;
    --royal-deep: #17127a;
    --royal-bright: #3b33c4;
    --ink: #3a3a48;
    --paper: #fbfbfe;
    --paper-tint: #eeeef8;
    --silver: #e8e8f2;
    --backdrop: #1c1c1f;
  }
  html, body {
    margin: 0;
    padding: 0;
    width: 1200px;
    height: 1024px;
    overflow: hidden;
    background: var(--backdrop);
  }
  .canvas {
    width: 1200px;
    height: 1024px;
    display: flex;
    flex-direction: column;
    align-items: center;
    justify-content: center;
    gap: 24px;
  }
  .card {
    position: relative;
    width: 840px;
    height: 480px;
    overflow: hidden;
    box-sizing: border-box;
  }
  .card-pattern {
    position: absolute;
    inset: 0;
  }
  /* Front */
  .card-front .card-pattern {
    background: radial-gradient(ellipse at 40% 45%, var(--paper) 0%, var(--paper-tint) 100%);
  }
  .front-content {
    position: relative;
    padding: 56px 64px;
    font-family: "Lora", serif;
    color: var(--royal);
  }
  .brand-name {
    font-family: "Lora", serif;
    font-weight: 500;
    font-size: 44px;
    line-height: 1.1;
    margin: 0;
    color: var(--royal);
  }
  .rep-name {
    display: flex;
    align-items: center;
    gap: 12px;
    margin: 18px 0 22px;
    font-size: 26px;
  }
  .divider {
    height: 2px;
    background: var(--royal);
    opacity: 0.85;
  }
  .contact-list {
    list-style: none;
    margin: 20px 0 22px;
    padding: 0;
    font-size: 24px;
    color: var(--ink);
  }
  .contact-list li {
    display: flex;
    align-items: center;
    gap: 12px;
    margin: 8px 0;
  }
  .contact-list .sep { width: 10px; }
  .icon { flex: none; }
  /* Back */
  .card-back .card-pattern {
    background: radial-gradient(ellipse at 45% 40%, var(--royal-bright) 0%, var(--royal) 50%, var(--royal-deep) 100%);
  }
  .back-url {
    position: absolute;
    top: 44px;
    left: 56px;
    font-family: "Open Sans", sans-serif;
    font-size: 18px;
    color: var(--silver);
  }
  .back-brand {
    position: absolute;
    inset: 0;
    display: flex;
    align-items: center;
    justify-content: center;
    font-family: "Lora", serif;
    font-weight: 500;
    font-size: 50px;
    color: var(--silver);
  }
</style>
</head>
<body>
<main class="canvas">

  <section class="card card-front">
    <div class="card-pattern" role="img" aria-label="Faint lavender floral damask pattern on white card stock"></div>
    <div class="front-content">
      <h1 class="brand-name">Marlow Avery Fine Jewelry</h1>
      <div class="rep-name">
        <svg class="icon" width="18" height="18" viewBox="0 0 18 18"><circle cx="9" cy="9" r="8" fill="var(--royal)"/></svg>
        <span>Marlow Avery Pennington</span>
      </div>
      <div class="divider"></div>
      <ul class="contact-list">
        <li>
          <svg class="icon" width="22" height="22" viewBox="0 0 22 22"><path d="M2 11 L11 3 L20 11 H17 V19 H13 V14 H9 V19 H5 V11 Z" fill="var(--royal)"/></svg>
          <span>2280 Seabright Avenue Harbor City, FL 32999</span>
        </li>
        <li>
          <svg class="icon" width="22" height="22" viewBox="0 0 22 22"><rect x="6" y="2" width="10" height="18" rx="2" fill="none" stroke="var(--royal)" stroke-width="2"/><circle cx="11" cy="16.5" r="1.2" fill="var(--royal)"/></svg>
          <span>000-000-000</span>
          <span class="sep"></span>
          <svg class="icon" width="22" height="22" viewBox="0 0 22 22"><rect x="2" y="5" width="18" height="12" fill="var(--royal)"/><path d="M2 5 L11 12 L20 5" fill="none" stroke="#fff" stroke-width="1.5"/></svg>
          <span>marlow@marlowaveryjewelry.com</span>
        </li>
        <li>
          <svg class="icon" width="22" height="22" viewBox="0 0 22 22"><circle cx="11" cy="11" r="9" fill="none" stroke="var(--royal)" stroke-width="2"/><ellipse cx="11" cy="11" rx="4" ry="9" fill="none" stroke="var(--royal)" stroke-width="1.5"/><path d="M2 11 H20" stroke="var(--royal)" stroke-width="1.5"/></svg>
          <span>www.marlowaveryjewelry.com</span>
        </li>
      </ul>
      <div class="divider"></div>
    </div>
  </section>

  <section class="card card-back">
    <div class="card-pattern" role="img" aria-label="Royal blue card with a subtle tone-on-tone floral damask pattern"></div>
    <div class="back-url">www.marlowaveryjewelry.com</div>
    <div class="back-brand">Marlow Avery Fine Jewelry</div>
  </section>

</main>
</body>
</html>
```